Mortgage Company ready to make a statement!

We have a basic logo that I am fairly happy with ... but it could use a little bit of tweaking before we order the sign for our building. We also want some knock-your-socks-off business cards.
Problem: Inside of our Mortgage Office (Bright Fern Mortgage Group), we are going to have a coffee lounge (Sunbrew Cafe) for Realtors to use instead of the local Cuppington to meet with homebuyers. The office and coffee lounge are in an industrial building and is decorated with cozy overstuffed chairs, a hodge podge of interesting lamps and furniture, and goal is to make it as inviting as possible. However, we are a financial institution... so we need to keep it pretty clean as well.
One of my favorite marketing ideas is to cut a house key for everyone who buys a home using us with a key that matches our logo. There's only one key shape that works really well, so that needs to match the logo in order for the idea to work. I'll attach an image of the key blank.... although the way the key hole cut out looks terrible, so I was thinking of having them just do a thin outline instead.
Would like a similar, matching logo for the Sunbrew Cafe... but possibly something that would be a little less formal and would be cute on a coffee mug- nothing stuffy.
AND, we're opening a home inspection company as well, and we would like that logo and branding to match. The home inspection company is "Bright Fern Home Inspections"
We were thinking that for the home inspection company , we could use a magnifying glass shape inside of the house shape for the logo, use a keyhole shape inside of the same house for the mortgage company, and use a coffee cup inside of the house shape for Sunbrew Cafe.
Just getting stuck and need to help. I designed the attached logo myself, and that is what we are currently using. Designers at local printing companies have failed to impress us.
The mortgage industry has a lot of numbers and logos, etc that they require us to put on our business cards... so it's hard to keep them looking clean.
HELP! HELP! :)

```html
<!DOCTYPE html>
<html lang="en">
<head>
<meta charset="utf-8">
<title>Bright Fern Mortgage Group – Business Card</title>
<link rel="stylesheet" href="https://fonts.googleapis.com/css2?family=Jost:wght@400;500;600&family=Marcellus&display=swap">
<style>
  :root {
    --backdrop: #2b2b2d;
    --card: #1c1c1e;
    --ink-light: #f2f2f2;
    --ink-blue: #2e6b92;
    --icon-blue: #3a7aa6;
  }
  * { margin: 0; padding: 0; box-sizing: border-box; }
  html, body {
    width: 1200px; height: 900px; overflow: hidden;
    background: var(--backdrop);
  }
  .canvas {
    position: relative; width: 1200px; height: 900px;
  }
  .card {
    position: absolute; left: 250px; width: 700px; height: 400px;
    background: var(--card);
    box-shadow: 0 10px 30px rgba(0,0,0,0.45);
  }
  .card--front { top: 40px; }
  .card--back { top: 460px; }

  .brand {
    position: absolute; left: 0; right: 0; top: 170px;
    display: flex; align-items: center; justify-content: center; gap: 16px;
  }
  .brand__square {
    width: 34px; height: 34px; border: none; background: var(--ink-light);
  }
  .brand__name {
    font-family: "Jost", sans-serif; font-weight: 400;
    font-size: 40px; color: var(--ink-light); letter-spacing: 0.5px;
  }

  .contact-block {
    position: absolute; top: 150px; left: 120px;
    display: flex; align-items: stretch;
  }
  .person { text-align: right; padding-right: 26px; }
  .person__name {
    font-family: "Marcellus", serif; font-size: 30px;
    color: var(--ink-blue); letter-spacing: 1px; line-height: 1.1;
  }
  .person__title {
    font-family: "Jost", sans-serif; font-weight: 600;
    font-size: 20px; color: var(--ink-light); letter-spacing: 1px; margin-top: 8px;
  }
  .divider { width: 2px; background: var(--ink-blue); margin: 14px 0 -4px; }
  .details {
    list-style: none; padding-left: 24px; padding-top: 12px;
    font-family: "Jost", sans-serif; font-size: 18px;
    color: var(--ink-light); letter-spacing: 1.2px;
  }
  .details li { display: flex; align-items: center; gap: 14px; height: 26px; }
  .details svg { width: 16px; height: 16px; flex: none; }
  .address {
    position: absolute; left: 120px; bottom: 80px;
    font-family: "Jost", sans-serif; font-size: 18px;
    color: var(--ink-light); letter-spacing: 1.2px;
  }
</style>
</head>
<body>
<main class="canvas">
  <section class="card card--front">
    <div class="brand">
      <span class="brand__square" aria-hidden="true"></span>
      <span class="brand__name">Bright Fern Mortgage Group</span>
    </div>
  </section>

  <section class="card card--back">
    <div class="contact-block">
      <div class="person">
        <p class="person__name">COLIN MARSH</p>
        <p class="person__title">CEO</p>
      </div>
      <div class="divider"></div>
      <ul class="details">
        <li>
          <svg viewBox="0 0 16 16" aria-hidden="true"><rect x="4" y="1" width="8" height="14" rx="1.5" fill="none" stroke="var(--icon-blue)" stroke-width="1.4"/><line x1="7" y1="12.5" x2="9" y2="12.5" stroke="var(--icon-blue)" stroke-width="1.2"/></svg>
          000-555-0142
        </li>
        <li>
          <svg viewBox="0 0 16 16" aria-hidden="true"><rect x="4" y="1" width="8" height="5" fill="var(--icon-blue)"/><rect x="1" y="6" width="14" height="6" rx="1" fill="var(--icon-blue)"/><rect x="4" y="10" width="8" height="5" fill="var(--card)" stroke="var(--icon-blue)" stroke-width="1.2"/></svg>
          000-555-0143
        </li>
        <li>
          <svg viewBox="0 0 16 16" aria-hidden="true"><rect x="1" y="3" width="14" height="10" fill="var(--icon-blue)"/><polyline points="1,3 8,9 15,3" fill="none" stroke="var(--card)" stroke-width="1.3"/></svg>
          colin.marsh@brightfernmg.com
        </li>
      </ul>
    </div>
    <p class="address">Laneway Plaza Sydney Melbourne</p>
  </section>
</main>
</body>
</html>
```